U.S. Popcorn company needs business cards

We are a popcorn company that manufactures popcorn and sells it to grocery stores worldwide. Our theme is "Americana" and our logo is U.S. route 66 which is the most famous highway in the U.S.

We would like the design to be simple and to use both sides. On the back side we would like to see just the logo and website. The front would be normal details

Target Market(s)

Wholesalers, grocers and distributors

Industry/Entity Type

Manufacture

Contact Information for Business Card

Business name: Prairie Lantern Popcorn
Phone: +1 555 308 4726
Email: Dale@prairielanternpopcorn.com
website: www.prairielanternpopcorn.com
Tag Line: "POPular for a reason"
Name: Dale Whitcombe
Title: Founder/President

Requirements
Must have
• Either this design should be fun or clean and simple. I will let you show me your thougths.
Nice to have
• Anything that ties in the real Hwy Route 66.
• Colors might need to be red, white and blue incorporated.
Should not have
• Not be too busy.

```html
<!DOCTYPE html>
<html lang="en">
<head>
<meta charset="utf-8">
<title>Prairie Lantern Popcorn – Business Card</title>
<link href="https://fonts.googleapis.com/css2?family=Lato:wght@400;700&display=swap" rel="stylesheet">
<style>
  :root {
    --stage: #222222;
    --paper: #ffffff;
    --navy: #23306a;
    --red: #e32028;
  }
  * { margin: 0; padding: 0; box-sizing: border-box; }
  html, body {
    width: 1189px; height: 1200px; overflow: hidden;
    background: var(--stage);
    font-family: "Lato", sans-serif;
    color: var(--navy);
  }
  .card {
    position: absolute; left: 171px;
    width: 856px; height: 488px;
    background: var(--paper);
    overflow: hidden;
  }
  .card--back { top: 67px; }
  .card--front { top: 626px; }

  .brand-mark {
    position: absolute;
    display: flex; align-items: center; gap: 14px;
    font-weight: 700; color: var(--navy);
  }
  .brand-mark__dot {
    flex: none; border-radius: 50%; background: var(--red);
  }
  .card--back .brand-mark {
    left: 0; right: 0; top: 180px; justify-content: center;
    font-size: 40px;
  }
  .card--back .brand-mark__dot { width: 34px; height: 34px; }

  .website { position: absolute; font-size: 21px; white-space: nowrap; }
  .website__domain { color: var(--red); }
  .card--back .website { left: 0; right: 0; top: 361px; text-align: center; }

  .name-tab {
    position: absolute; left: 0; top: 38px;
    width: 288px; height: 82px;
    background: var(--navy);
    border-radius: 0 41px 41px 0;
    padding: 14px 0 0 33px;
    white-space: nowrap;
  }
  .name-tab__name { color: var(--paper); font-size: 29px; line-height: 1.05; }
  .name-tab__title { color: var(--red); font-size: 22px; line-height: 1.05; }

  .company { position: absolute; left: 31px; top: 186px; font-size: 34px; font-weight: 700; white-space: nowrap; }
  .tagline { position: absolute; left: 32px; top: 230px; font-size: 22px; }
  .address { position: absolute; left: 33px; top: 290px; font-size: 22px; line-height: 29px; }
  .contact { position: absolute; left: 33px; top: 360px; font-size: 22px; line-height: 28px; list-style: none; white-space: nowrap; }
  .contact li { display: flex; align-items: center; gap: 10px; }
  .contact svg { width: 25px; height: 25px; flex: none; }
  .card--front .website { left: 31px; top: 443px; }

  .card--front .brand-mark {
    left: 560px; width: 256px; top: 300px;
    font-size: 30px; line-height: 1.15; justify-content: center;
  }
  .card--front .brand-mark__dot { width: 26px; height: 26px; }

  .accent-bar {
    position: absolute; left: 95px; bottom: 0;
    width: 189px; height: 5px; background: var(--red);
  }
</style>
</head>
<body>

<section class="card card--back">
  <div class="brand-mark">
    <span class="brand-mark__dot"></span>
    <span>Prairie Lantern Popcorn</span>
  </div>
  <p class="website">www.<span class="website__domain">prairielanternpopcorn</span>.com</p>
</section>

<section class="card card--front">
  <div class="name-tab">
    <p class="name-tab__name">Dale Whitcombe</p>
    <p class="name-tab__title">Founder/President</p>
  </div>

  <h1 class="company">Prairie Lantern Popcorn</h1>
  <p class="tagline">POPular for a reason</p>

  <p class="address">Maple Hollow, KS<br>United States</p>

  <ul class="contact">
    <li>
      <svg viewBox="0 0 24 24" aria-hidden="true">
        <rect width="24" height="24" rx="3" fill="#e32028"/>
        <path d="M8 5c1 0 2 3 2 4s-1.5 1-1 2.5 2 3.5 3.5 4 1.5-1 2.5-1 4 1 4 2-1.5 2.5-3 2.5C10 19 5 13 5 8c0-1.5 1.5-3 3-3z" fill="#fff"/>
      </svg>
      <span>+1 555 308 4726</span>
    </li>
    <li>
      <svg viewBox="0 0 24 24" aria-hidden="true">
        <rect width="24" height="24" rx="3" fill="#e32028"/>
        <rect x="4" y="7" width="16" height="11" fill="none" stroke="#fff" stroke-width="1.6"/>
        <path d="M4 7l8 6 8-6" fill="none" stroke="#fff" stroke-width="1.6"/>
      </svg>
      <span>Dale@prairielanternpopcorn.com</span>
    </li>
  </ul>

  <p class="website">www.<span class="website__domain">prairielanternpopcorn</span>.com</p>

  <div class="brand-mark">
    <span class="brand-mark__dot"></span>
    <span>Prairie Lantern<br>Popcorn</span>
  </div>

  <div class="accent-bar"></div>
</section>

</body>
</html>
```